Copper lark buildworks

Copper lark buildworks is a small construction company.
Who is a licenced builder, Carpenter, joiner,
working on heritage ,new build, speacial projects and sometimes furniture

Industry/Entity Type

Construction

```html
<!DOCTYPE html>
<html lang="en">
<head>
<meta charset="utf-8">
<title>Copper lark buildworks – business cards</title>
<link href="https://fonts.googleapis.com/css2?family=Open+Sans:wght@400;600&display=swap" rel="stylesheet">
<style>
  :root {
    --lime: #8cc63f;
    --ink: #111111;
    --paper: #ffffff;
    --stage: #e9e7e2;
    --muted: #2b2b2b;
  }
  * { box-sizing: border-box; margin: 0; padding: 0; }
  html, body { width: 1200px; height: 880px; overflow: hidden; background: var(--stage); }
  body { position: relative; font-family: "Open Sans", Arial, sans-serif; }

  .card {
    position: absolute;
    width: 620px;
    height: 360px;
    border-radius: 22px;
    overflow: hidden;
    box-shadow: 0 10px 28px rgba(0,0,0,0.18);
  }

  /* Front */
  .card-front { left: 110px; top: 50px; background: var(--lime); }
  .front-brand {
    position: absolute; left: 0; right: 0; top: 138px;
    display: flex; align-items: center; justify-content: center; gap: 14px;
  }
  .brand-dot { width: 30px; height: 30px; border-radius: 50%; background: var(--ink); flex: none; }
  .brand-name { font-weight: 600; font-size: 36px; color: var(--ink); letter-spacing: 0.2px; white-space: nowrap; }
  .front-url {
    position: absolute; left: 0; right: 0; top: 222px; text-align: center;
    color: var(--paper); font-size: 15px; letter-spacing: 4px;
  }

  /* Back */
  .card-back { left: 470px; top: 470px; background: var(--paper); }
  .back-shapes { position: absolute; inset: 0; }
  .person { position: absolute; right: 34px; top: 26px; text-align: right; color: var(--paper); }
  .person-name { font-size: 22px; font-weight: 400; }
  .person-name .surname { color: var(--lime); }
  .person-role { font-size: 14px; margin-top: -2px; }

  .back-brand {
    position: absolute; left: 38px; top: 190px;
    display: flex; align-items: center; gap: 12px;
  }
  .back-brand .brand-dot { width: 24px; height: 24px; background: var(--lime); }
  .back-brand .brand-name { font-size: 28px; color: var(--ink); }

  .rule { position: absolute; left: 38px; right: 38px; top: 250px; height: 1.5px; background: var(--lime); }

  .contacts {
    position: absolute; left: 38px; right: 38px; top: 272px;
    display: flex; align-items: center; justify-content: space-between;
    font-size: 13.5px; color: var(--muted);
  }
  .contact { display: flex; align-items: center; gap: 6px; white-space: nowrap; }
  .contact svg { width: 17px; height: 17px; flex: none; }
  .divider { width: 1.5px; height: 22px; background: var(--lime); flex: none; }
</style>
</head>
<body>

  <section class="card card-front">
    <div class="front-brand">
      <span class="brand-dot"></span>
      <span class="brand-name">Copper lark buildworks</span>
    </div>
    <p class="front-url">www.copperlarkbuild.com</p>
  </section>

  <section class="card card-back">
    <svg class="back-shapes" viewBox="0 0 620 360" preserveAspectRatio="none">
      <path d="M0,0 H620 V128 Q420,40 0,168 Z" fill="var(--ink)"/>
      <path d="M0,176 Q420,48 620,140 L620,148 Q420,62 0,186 Z" fill="var(--lime)"/>
    </svg>

    <div class="person">
      <p class="person-name">Marcus <span class="surname">Hale</span></p>
      <p class="person-role">President</p>
    </div>

    <div class="back-brand">
      <span class="brand-dot"></span>
      <span class="brand-name">Copper lark buildworks</span>
    </div>

    <div class="rule"></div>

    <div class="contacts">
      <span class="contact">
        <svg viewBox="0 0 20 20" fill="none" stroke="var(--lime)" stroke-width="1.6">
          <circle cx="10" cy="10" r="8.5"/>
          <rect x="7" y="5" width="6" height="10" rx="1"/>
        </svg>
        0491570236
      </span>
      <span class="divider"></span>
      <span class="contact">
        <svg viewBox="0 0 20 20" fill="none" stroke="var(--lime)" stroke-width="1.6">
          <circle cx="10" cy="10" r="8.5"/>
          <rect x="5.5" y="7" width="9" height="6.5"/>
          <path d="M5.5,7 L10,11 L14.5,7"/>
        </svg>
        info@copperlarkbuild.com
      </span>
      <span class="divider"></span>
      <span class="contact">
        <svg viewBox="0 0 20 20" fill="none" stroke="var(--lime)" stroke-width="1.6">
          <circle cx="10" cy="10" r="8.5"/>
          <circle cx="10" cy="10" r="5"/>
          <path d="M5,10 H15 M10,5 V15"/>
        </svg>
        www.copperlarkbuild.com
      </span>
    </div>
  </section>

</body>
</html>
```